Animal Eye Clinic needs a Business card

We are a new veterinary ophthalmology practice (Ridgeline Pet Vision Care) and we need a business card designed. We only see animal eyes - we are not a regular veterinary clinic. We already have a logo. We are looking for a professional, good looking business card to hand out to our clients. We are looking for something simple but professional and contemporary. Our logo is likely the only picture/graphic that needs to be on the card.
Updates

Contact Information for Business Card

Delia Vossman, BSc, DVM, MSc, DipACVO
Veterinary Ophthalmologist

Phone: 250.418.3927
Email: ridgelinepetvisioncare@mailbox-example.net
Website: ridgelinepetvisioncare-example.net
Address: 1874 Thornbury Rd
Kelowna, BC, V1X 4M9

Colors

Designer to choose colors to be used in the design.

Requirements
Must have
• Our logo (attached)

```html
<!DOCTYPE html>
<html lang="en">
<head>
<meta charset="utf-8">
<title>Ridgeline Pet Vision Care – Business Card</title>
<link href="https://fonts.googleapis.com/css2?family=Roboto:wght@400;500;700&display=swap" rel="stylesheet">
<style>
  :root {
    --teal: #0f8c9b;
    --teal-dark: #0a7382;
    --grey: #7a7a7a;
    --ink: #3c3c3c;
    --paper: #ffffff;
    --backdrop: #3a322e;
  }
  * { box-sizing: border-box; margin: 0; padding: 0; }
  html, body { width: 1200px; height: 847px; overflow: hidden; }
  body {
    background: var(--backdrop);
    font-family: "Roboto", Arial, sans-serif;
    position: relative;
  }
  .card {
    position: absolute;
    width: 540px;
    height: 309px;
    background: var(--paper);
    border-bottom: 5px solid var(--teal);
    box-shadow: 0 10px 24px rgba(0,0,0,.45);
    overflow: hidden;
  }
  .card--front { left: 50px; top: 90px; }
  .card--back { left: 610px; top: 448px; }

  .brand { display: flex; align-items: center; gap: 12px; color: var(--teal); font-weight: 500; }
  .brand__dot { border-radius: 50%; background: var(--teal); flex: none; }
  .card--front .brand {
    position: absolute; left: 0; right: 0; top: 132px; justify-content: center;
    font-size: 27px;
  }
  .card--front .brand__dot { width: 30px; height: 30px; }

  .card--back .brand { position: absolute; left: 28px; top: 24px; font-size: 17px; gap: 9px; }
  .card--back .brand__dot { width: 20px; height: 20px; }

  .contact { position: absolute; left: 28px; top: 72px; width: 300px; }
  .contact__name {
    color: var(--teal); font-weight: 700; font-size: 18px; letter-spacing: 1.5px;
    text-transform: uppercase;
  }
  .contact__credentials { color: var(--teal); font-size: 12.5px; margin-top: 3px; }
  .contact__role { color: var(--ink); font-size: 12.5px; margin-top: 2px; }
  .contact__address { color: var(--ink); font-size: 12.5px; line-height: 1.45; margin-top: 14px; }
  .contact__lines { list-style: none; margin-top: 10px; color: var(--ink); font-size: 12px; line-height: 1.6; }
  .contact__lines li { display: flex; align-items: center; gap: 6px; white-space: nowrap; }
  .contact__lines svg { width: 11px; height: 11px; flex: none; fill: var(--teal); }

  .artwork {
    position: absolute; right: 0; bottom: 0; width: 230px; height: 240px;
    border-top-left-radius: 120px;
    background: linear-gradient(160deg, var(--teal) 0%, var(--teal-dark) 65%, var(--grey) 100%);
  }
</style>
</head>
<body>
  <section class="card card--front" aria-label="Card front">
    <div class="brand"><span class="brand__dot"></span><span>Ridgeline Pet Vision Care</span></div>
  </section>

  <section class="card card--back" aria-label="Card back">
    <div class="brand"><span class="brand__dot"></span><span>Ridgeline Pet Vision Care</span></div>

    <div class="contact">
      <p class="contact__name">Delia Vossman</p>
      <p class="contact__credentials">BSc, DVM, MSc, DipACVO</p>
      <p class="contact__role">Veterinary Ophthalmologist</p>
      <p class="contact__address">1874 Thornbury Rd<br>Kelowna, BC, V1X 4M9</p>
      <ul class="contact__lines">
        <li><svg viewBox="0 0 24 24"><path d="M6.6 10.8a15.1 15.1 0 0 0 6.6 6.6l2.2-2.2a1 1 0 0 1 1-.25 11.4 11.4 0 0 0 3.6.57 1 1 0 0 1 1 1V20a1 1 0 0 1-1 1A17 17 0 0 1 3 4a1 1 0 0 1 1-1h3.5a1 1 0 0 1 1 1c0 1.25.2 2.45.57 3.57a1 1 0 0 1-.25 1z"/></svg>250.418.3927</li>
        <li><svg viewBox="0 0 24 24"><path d="M2 5h20v14H2z M2 5l10 8 10-8" /></svg>ridgelinepetvisioncare@mailbox-example.net</li>
        <li><svg viewBox="0 0 24 24"><circle cx="12" cy="12" r="10"/></svg>ridgelinepetvisioncare-example.net</li>
      </ul>
    </div>

    <div class="artwork" role="img" aria-label="Illustration of a horse, dog and cat in profile"></div>
  </section>
</body>
</html>
```